Business Card Design for company

We want new business cards. We'd like something different-- yet still highly professional. Our tagline is Providing leadership, delivering success. Stock photos are ok, as long as they are relevant and look upscale.

Target Market(s)

Architecture/Business Management Consulting/Engineering Consulting

Contact Information for Business Card

dark gray background with pops of blue might be good, but you tell me. You're the designers. Rounded corners might be nice, but again, you tell me.

Font styles to use
Serif
Sans Serif

Colors
3276b5
5c5c5c
9d9d9d
fbfbfb

Requirements
Nice to have
• Something different, but still very professional.

```html
<!DOCTYPE html>
<html lang="en">
<head>
<meta charset="utf-8">
<title>Norvale Partners – Business Card</title>
<link rel="stylesheet" href="https://fonts.googleapis.com/css2?family=Open+Sans:wght@400;600&display=swap">
<style>
  :root {
    --blue: #3276b5;
    --blue-deep: #225f99;
    --dark: #3d3d3d;
    --mid: #5c5c5c;
    --light: #9d9d9d;
    --paper: #fbfbfb;
    --backdrop: #e6e4e0;
  }
  html, body {
    margin: 0;
    width: 1200px;
    height: 1023px;
    overflow: hidden;
    background: var(--backdrop);
  }
  .card {
    position: absolute;
    left: 100px;
    top: 226px;
    width: 1000px;
    height: 571px;
    background: var(--paper);
    box-shadow: 0 10px 30px rgba(0,0,0,.18);
    font-family: "Open Sans", Arial, sans-serif;
    overflow: hidden;
  }
  .card-shapes { position: absolute; inset: 0; }
  .brand {
    position: absolute;
    left: 90px;
    top: 230px;
    display: flex;
    align-items: center;
    gap: 18px;
  }
  .brand-mark {
    width: 22px;
    height: 22px;
    background: var(--blue);
  }
  .brand-name {
    font-weight: 600;
    color: var(--mid);
    font-size: 46px;
    letter-spacing: 3px;
    line-height: 1;
    text-transform: uppercase;
  }
  .holder {
    position: absolute;
    left: 470px;
    top: 440px;
    width: 300px;
    text-align: center;
    color: var(--paper);
  }
  .holder-name { font-size: 34px; font-weight: 600; line-height: 1.1; }
  .holder-role { font-size: 22px; opacity: .9; }
  .contact {
    position: absolute;
    left: 690px;
    top: 190px;
    margin: 0;
    padding: 0;
    list-style: none;
    color: var(--paper);
    font-size: 21px;
    line-height: 1.35;
  }
  .contact li { display: flex; align-items: flex-start; gap: 12px; margin-bottom: 4px; }
  .contact svg { flex: none; margin-top: 5px; }
</style>
</head>
<body>
  <main class="card">
    <svg class="card-shapes" viewBox="0 0 1000 571" width="1000" height="571" aria-hidden="true">
      <polygon class="band-dark" points="445,300 1000,300 1000,571 420,571" fill="var(--dark)"/>
      <polygon class="band-blue" points="560,165 1000,165 1000,470 760,470" fill="var(--blue)"/>
      <polygon class="wedge-white" points="760,470 1000,470 1000,571 900,571" fill="var(--paper)"/>
      <polygon class="wedge-grey" points="790,490 1000,490 1000,571 930,571" fill="var(--light)"/>
    </svg>

    <div class="brand">
      <span class="brand-mark"></span>
      <span class="brand-name">Norvale<br>Partners</span>
    </div>

    <div class="holder">
      <div class="holder-name">Daniel Reyes</div>
      <div class="holder-role">Owner</div>
    </div>

    <ul class="contact">
      <li>
        <svg width="18" height="18" viewBox="0 0 18 18"><rect width="18" height="18" rx="3" fill="var(--paper)"/><path d="M5 4l2 0 1 3-1.5 1a7 7 0 0 0 3.5 3.5l1-1.5 3 1v2c-5 1-10-4-9-9z" fill="var(--blue)"/></svg>
        <span>+0000-0000-0000</span>
      </li>
      <li>
        <svg width="18" height="18" viewBox="0 0 18 18"><rect width="18" height="18" rx="3" fill="var(--paper)"/><rect x="3.5" y="5" width="11" height="8" fill="none" stroke="var(--blue)" stroke-width="1.5"/><path d="M3.5 5l5.5 5 5.5-5" fill="none" stroke="var(--blue)" stroke-width="1.5"/></svg>
        <span>info@yourdomain.com</span>
      </li>
      <li>
        <svg width="18" height="18" viewBox="0 0 18 18"><rect width="18" height="18" rx="3" fill="var(--paper)"/><circle cx="9" cy="9" r="5" fill="none" stroke="var(--blue)" stroke-width="1.5"/><path d="M4 9h10M9 4v10" stroke="var(--blue)" stroke-width="1.2"/></svg>
        <span>www.yourdomain.com</span>
      </li>
      <li>
        <svg width="18" height="18" viewBox="0 0 18 18"><rect width="18" height="18" rx="3" fill="var(--paper)"/><path d="M9 3.5a4 4 0 0 1 4 4c0 3-4 7-4 7s-4-4-4-7a4 4 0 0 1 4-4z" fill="var(--blue)"/><circle cx="9" cy="7.5" r="1.4" fill="var(--paper)"/></svg>
        <span>Studio 210,<br>48 Harrow Lane,<br>Leeds</span>
      </li>
    </ul>
  </main>
</body>
</html>
```